Brell Stone Company Business Cards

Front and Back Business Card - logo and text setup - cool design. I need workable photoshop or illustrator files so I can setup each employee card with design that is created
Updates

Hi everyone, thank you for the great entries. Please no more white and blue cards - there are so many already - black and silver only now please. thanks!

Target Market(s)

Construction Industry - Facility Managers

Industry/Entity Type

Construction

Contact Information for Business Card

I really like contemporary simplistic looks - clean neat....not opposed to seeing some black backrounds

Requirements
Must have
• Logo/website address with design on front only - www.brellstone-example.com (logo attached)
• Back:
• Name/Title/Company Address/Phone/email address
Nice to have
• Cool design
Should not have
• Nothing gimmicky like Fire or Water - since we are a Fire Protection company - it has all been done

```html
<!DOCTYPE html>
<html lang="en">
<head>
<meta charset="utf-8">
<title>Brell Stone Company Business Cards</title>
<link rel="stylesheet" href="https://fonts.googleapis.com/css2?family=Arimo:wght@400;700&display=swap">
<style>
  :root {
    --stage: #1d1d20;
    --warm: #ea4b35;
    --cool: #2b4279;
    --navy: #1f3a78;
    --accent: #ec4f34;
    --paper: #ffffff;
    --white: #ffffff;
  }
  * { margin: 0; padding: 0; box-sizing: border-box; }
  html, body { width: 1200px; height: 800px; overflow: hidden; }
  body {
    background: var(--stage);
    font-family: "Arimo", Arial, sans-serif;
    position: relative;
  }
  .card {
    position: absolute;
    width: 525px;
    height: 300px;
    border-radius: 3px;
    overflow: hidden;
    box-shadow: 0 18px 40px rgba(0,0,0,0.5);
  }
  /* Front */
  .card-front {
    left: 50px; top: 250px;
    background: linear-gradient(150deg, var(--warm) 0%, #b24950 40%, #6a4472 65%, var(--cool) 100%);
    color: var(--white);
    display: flex; flex-direction: column; align-items: center; justify-content: center;
  }
  .brand-name {
    font-weight: 700;
    font-size: 54px;
    letter-spacing: -1px;
    line-height: 1;
    display: flex; align-items: center; gap: 14px;
  }
  .brand-mark {
    width: 16px; height: 16px; background: var(--white);
  }
  .brand-web {
    margin-top: 26px;
    font-size: 14px;
    letter-spacing: 5px;
  }
  /* Back */
  .card-back {
    left: 625px; top: 250px;
    background: var(--paper);
  }
  .divider {
    position: absolute; left: 290px; top: 40px;
    width: 2px; height: 235px; background: var(--accent);
  }
  .squares-top { position: absolute; left: 40px; top: 40px; }
  .squares-bottom { position: absolute; left: 300px; top: 250px; }
  .person {
    position: absolute; right: 250px; top: 66px; text-align: right;
  }
  .person-name { color: var(--navy); font-weight: 700; font-size: 24px; }
  .person-title { color: var(--accent); font-size: 15px; margin-top: 2px; }
  .contact {
    position: absolute; left: 308px; top: 110px;
    color: var(--navy); font-size: 12.5px; line-height: 1.55;
    list-style: none;
  }
  .contact li { display: flex; align-items: center; gap: 6px; white-space: nowrap; }
  .contact .web { color: var(--accent); }
  .contact svg { width: 11px; height: 11px; flex: none; }
  .contact .plain { padding-left: 0; }
</style>
</head>
<body>
  <section class="card card-front" aria-label="Card front">
    <div class="brand-name"><span class="brand-mark"></span>Brell Stone</div>
    <div class="brand-web">www.brellstone-example.com</div>
  </section>

  <section class="card card-back" aria-label="Card back">
    <svg class="squares-top" width="245" height="14" viewBox="0 0 245 14">
      <rect x="0" y="0" width="14" height="14" fill="#fbe3da"/>
      <rect x="23" y="0" width="14" height="14" fill="#f9d2c4"/>
      <rect x="46" y="0" width="14" height="14" fill="#f7c1ad"/>
      <rect x="69" y="0" width="14" height="14" fill="#f5ae96"/>
      <rect x="92" y="0" width="14" height="14" fill="#f39c80"/>
      <rect x="115" y="0" width="14" height="14" fill="#f18a6a"/>
      <rect x="138" y="0" width="14" height="14" fill="#ef7855"/>
      <rect x="161" y="0" width="14" height="14" fill="#ee6848"/>
      <rect x="184" y="0" width="14" height="14" fill="#ed5c3e"/>
      <rect x="207" y="0" width="14" height="14" fill="#ec5438"/>
      <rect x="230" y="0" width="14" height="14" fill="var(--accent)"/>
    </svg>
    <div class="person">
      <div class="person-name">Mara Colby</div>
      <div class="person-title">Director</div>
    </div>
    <div class="divider"></div>
    <ul class="contact">
      <li class="plain">PO BOX 418, Harbor Road</li>
      <li class="plain">Ashfield</li>
      <li><svg viewBox="0 0 12 12"><rect x="2" y="1" width="8" height="10" rx="1.5" fill="none" stroke="var(--accent)" stroke-width="1.4"/></svg>(555) 014 2290</li>
      <li><svg viewBox="0 0 12 12"><rect x="0.5" y="2" width="11" height="8" fill="var(--accent)"/><path d="M0.5 2 L6 7 L11.5 2" fill="none" stroke="#fff" stroke-width="1"/></svg>info@brellstone-example.com</li>
      <li><svg viewBox="0 0 12 12"><circle cx="6" cy="6" r="5" fill="none" stroke="var(--accent)" stroke-width="1.2"/><path d="M1 6 H11 M6 1 V11" stroke="var(--accent)" stroke-width="1"/></svg><span class="web">www.brellstone-example.com</span></li>
    </ul>
    <svg class="squares-bottom" width="200" height="14" viewBox="0 0 200 14">
      <rect x="0" y="0" width="14" height="14" fill="var(--accent)"/>
      <rect x="23" y="0" width="14" height="14" fill="#ed5c3e"/>
      <rect x="46" y="0" width="14" height="14" fill="#ef7855"/>
      <rect x="69" y="0" width="14" height="14" fill="#f18a6a"/>
      <rect x="92" y="0" width="14" height="14" fill="#f39c80"/>
      <rect x="115" y="0" width="14" height="14" fill="#f5ae96"/>
      <rect x="138" y="0" width="14" height="14" fill="#f7c1ad"/>
      <rect x="161" y="0" width="14" height="14" fill="#f9d2c4"/>
      <rect x="184" y="0" width="14" height="14" fill="#fbe3da"/>
    </svg>
  </section>
</body>
</html>
```